Brellix Dwellings from US$9,995– Making buying a house as easy as ordering a pizza online - worldwide

I am after a website that is fun and interactive.

Buying a house should be as simple as buying a Pizza delivery online.....

Tidewell 20' ………………………………………….US$9,995
Standard, 30sqm Studio with kitchen & Bathroom, Flat Roof
Amber Ridge 20' ………………………………………….US$11,995
Standard, 30sqm Studio with kitchen & Bathroom, Pitched Roof
Lanternfield 40' ………………………………………….US$18,995
Standard, 60sqm, 2 Bedrooms, Lounge, kitchen & Bathroom, Flat Roof
Quillmoor 40' ………………………………………….US$20,995
Standard, 60sqm, 2 Bedrooms, Lounge, kitchen & Bathroom, Pitched Roof
Saltmeadow 40' ………………………………………….US$22,995
Beach design, 60sqm, 2 Bedrooms, Lounge, kitchen & Bathroom, Pitched Roof
The Brightfold 40' ………………………………………….US$24,995
Beach design, 60sqm, 2 Bedrooms, Lounge, kitchen, Bathroom, Deck, Pitched Roof

eg. https://www.grubtally.com.au/ https://www.crustvane.com

I want a fun design....

i want to reinvent how people DESIGN - BUILD and DELIVER housing

I want a SaaS solution for drop shipping pre-built houses.

The main campaign, we are offering 1,000 homes (to anywhere in the world) for US$9,995 + shipping

Just need to Pay a Fully refundable $100 Deposit to pre-register (so need a shopping cart & payment solution).

"Lane Skipper" - pay in full and jump the queue to get your Brellix months earlier.

The campaign is based on crowdsourcing - we need 1000 participants to pre-register - then everyone's orders will be filled .

The design is very simple...
HEADER
- The Story
- The Product
- Design our Own
- Pre-Register
- Contact Us

- Login
- Shopping Cart

FOOTER
- Privacy
- Terms & Conditions
- Investment
- Media
- NGO/Government
- Contact
- Sitemap

The important parts is that everyone who
- Subscribes
- Makes Contact
- Pre-registers
…in the system automatically gets an account (just need name and email address).
The user is then sent an email with details on how they can log back in at any time and see purchases, update profile (eg. Shipping address, contact details, etc....)

This data also needs to be sent to a CRM eg Hubspot for marketing to automate regular updates to all users.

It also needs to link to Facebook, LinkedIn , TikTok, Instagram, Twitter

You can get sample content from our old website https://kestrelbuilds.sitevaultpages.com/ - Plus I have attached updated content in this Brief.

The hero image should be a slider with videos and images with links to "Call to Action"

PLEASE NOTE: that "brellix" is a brand new product that we pre build offsite so when it is delivered, it is ready to move in to. So we need a whole new look and a new style

This is a wordpress site to be hosted on my server - Once completed I need full access to add, amend and update any pages, images products

I am very open to different colours - do not be limited by the colours in the logo.

I would be interested to see what you can do with NO white backgrounds. (This might look good or could look horrible)

And most importantly what will your design look like on mobile devices (phones / ipads)

SUCCESS (1) is getting the user to LOOK - DREAM - BUY (Or at least pre-register)

SUCCESS (2) it MUST look fun but still highly professional and TRUSTWORTHY to get the interest of investors to invest millions $$$$$

SUCCESS (3) we need to get "Inflencers / Bloggers" talking about Brellix - this could be done by a campaign to get a million likes and get a FREE home fo both the follower and the blogger

Target Market(s)

New home buyers (younger demographic), Families wanting to extend (middle aged)

Industry/Entity Type

Housing, Crowdsourcing, Drop shipping, SaaS technology

Coding

Coded - Design and coding required

Colors
0054AA
0677BA
7BADD7
CADEEF
E8F1F8
EE7325
F08F49
F5BC92
FAE3D3
FDF4ED

Requirements
Must have
• ecommerce, user accounts, social media & crm connections for crowdsourcing marketing, Call to actions
Nice to have
• $1,000,000
Should not have
• Do NOT complicate the funnel in the steps to sign-up

```html
<!DOCTYPE html>
<html lang="en">
<head>
<meta charset="utf-8">
<title>Brellix – Design, Build, Deliver</title>
<link href="https://fonts.googleapis.com/css2?family=Montserrat:ital,wght@0,400;0,500;0,600;0,700;0,800;1,400;1,500;1,600&display=swap" rel="stylesheet">
<style>
:root{
  --blue:#0a55ad;
  --red:#e8262f;
  --yellow:#f8e51c;
  --ink:#111111;
  --grey-text:#3a3a3a;
  --white:#ffffff;
  --footer:#000000;
  --ring:#5a5a5a;
}
*{box-sizing:border-box;margin:0;padding:0}
html,body{width:1200px;height:2757px;overflow:hidden}
body{font-family:'Montserrat',sans-serif;background:var(--footer);position:relative;color:var(--white)}
.abs{position:absolute}
.hero{left:0;top:0;width:1200px;height:720px;background:var(--blue)}
.brand{font-weight:800;color:var(--white);letter-spacing:1px;line-height:1}
.brand-name{font-size:48px}
.brand-tag{font-size:17px;letter-spacing:2px;margin-top:6px}
.login{left:963px;top:26px;font-weight:600;font-size:18px;display:flex;align-items:center;gap:5px}
.cart{left:1047px;top:17px;width:40px;height:40px;border-radius:50%;background:var(--yellow)}
.nav{left:451px;top:74px;display:flex;gap:24px;font-weight:600;font-size:17px}
.hero-title{left:105px;top:180px;font-weight:800;font-size:56px;line-height:59px;text-transform:uppercase}
.hero-title .hl{color:var(--yellow)}
.price{left:549px;top:156px;width:140px;height:140px;border-radius:50%;background:var(--ink);text-align:center;padding-top:33px}
.price b{display:block;font-size:32px;font-weight:800;border-bottom:2px solid var(--yellow);width:100px;margin:0 auto 6px;padding-bottom:3px}
.price span{font-size:18px}
.house{left:578px;top:170px;width:622px;height:485px;background:linear-gradient(135deg,#cfd4da,#f2f2f2 55%,#b9a58e);clip-path:polygon(0 40%,55% 8%,100% 30%,100% 60%,10% 100%)}
.contactless{left:114px;top:389px;font-style:italic;font-weight:600;font-size:19px}
.search{left:111px;top:430px;width:326px;height:63px;background:var(--white);color:#555;font-size:17px;padding:20px 0 0 20px;display:flex;gap:6px}
.search-btn{left:437px;top:430px;width:125px;height:63px;background:var(--red);font-weight:600;font-size:19px;text-align:center;line-height:63px}
.play{left:109px;top:532px;width:62px;height:62px;border-radius:50%;background:#5a6a80}
.watch{left:184px;top:553px;font-weight:600;font-size:18px}
.story{left:0;top:690px;width:1200px;height:810px;background:linear-gradient(90deg,#ffffff,#f4f4f4 40%,#cfcfcf)}
.sketch{left:0;top:785px;width:548px;height:590px;background:linear-gradient(135deg,#f6f6f6,#dcdcdc)}
.eyebrow{font-size:27px;font-weight:500}
.section-title{font-size:50px;font-weight:800;text-transform:uppercase;line-height:1.1}
.story-text{left:565px;top:810px;width:540px;color:var(--grey-text)}
.story-text .eyebrow{color:#444}
.story-text .section-title{color:var(--ink);margin:8px 0 26px}
.story-text p{font-size:16px;line-height:23px;margin-bottom:23px}
.ticks{list-style:none}
.ticks li{position:relative;padding-left:28px;font-size:16px;line-height:23px;margin-bottom:23px}
.ticks li::before{content:"";position:absolute;left:0;top:4px;width:15px;height:15px;border-radius:50%;background:var(--red)}
.ticks li::after{content:"";position:absolute;left:4px;top:8px;width:6px;height:3px;border-left:2px solid #fff;border-bottom:2px solid #fff;transform:rotate(-45deg)}
.btn{display:inline-block;border-radius:30px;font-weight:600;font-size:18px;text-align:center}
.read-more{left:565px;top:1362px;width:157px;height:59px;line-height:59px;background:var(--red)}
.register{left:0;top:1480px;width:1200px;height:840px;background:var(--red)}
.reg-text{left:110px;top:1570px;width:450px}
.reg-text .section-title{margin:10px 0 24px}
.ticks.light li{color:#fff;margin-bottom:26px;font-size:16.5px}
.ticks.light li::before{background:#fff}
.ticks.light li::after{border-color:var(--red)}
.kitchen{left:0;top:1890px;width:590px;height:410px;background:linear-gradient(135deg,#f2f2f2,#e8d6b3 60%,#b8b4a6);clip-path:polygon(0 3%,80% 0,98% 12%,100% 100%,0 100%)}
.field{left:616px;width:473px;height:50px;background:#fff;border-radius:3px;color:#555;font-size:16px;padding:15px 0 0 18px}
.choose{left:616px;top:1840px;font-size:30px;font-weight:700;color:var(--yellow)}
.radio{left:616px;width:500px;font-size:16.5px;line-height:25px;padding-left:29px}
.radio::before{content:"";position:absolute;left:0;top:3px;width:17px;height:17px;border:2px solid #fff;border-radius:50%}
.note{left:616px;width:470px;font-style:italic;font-size:14.5px;line-height:19px}
.submit{left:616px;top:2158px;width:123px;height:59px;line-height:59px;background:var(--ink)}
.foot-logo .brand-name{font-size:66px}
.foot-logo .brand-tag{font-size:23px;letter-spacing:3px}
.foot-col h4{font-size:19px;font-weight:700;margin-bottom:20px}
.foot-col li{list-style:none;font-size:16.5px;line-height:28.5px}
.contact-line{font-size:16.5px;line-height:22px;padding-left:18px;position:relative}
.contact-line svg{position:absolute;left:0;top:4px}
.rule{left:111px;top:2642px;width:978px;height:1px;background:#444}
.copy{left:111px;top:2682px;font-size:16px}
.socials{left:835px;top:2669px;display:flex;gap:6px}
.socials span{width:46px;height:46px;border-radius:50%;border:1px solid var(--ring)}
</style>
</head>
<body>

<section class="abs hero">
  <div class="abs brand" style="left:110px;top:30px">
    <div class="brand-name">BRELLIX</div>
    <div class="brand-tag">DESIGN - BUILD - DELIVER</div>
  </div>
  <div class="abs login"><svg width="12" height="14" viewBox="0 0 12 14"><path d="M3 6V4a3 3 0 0 1 6 0v2" fill="none" stroke="#fff" stroke-width="1.8"/><rect x="1" y="6" width="10" height="8" rx="1" fill="#fff"/></svg>Login</div>
  <div class="abs cart"><svg width="40" height="40" viewBox="0 0 40 40"><path d="M11 13h3l2 10h10l2-7H15" fill="none" stroke="#111" stroke-width="2.2"/><circle cx="17" cy="27" r="1.8" fill="#111"/><circle cx="25" cy="27" r="1.8" fill="#111"/></svg></div>
  <nav class="abs nav"><span>The Story</span><span>The Product</span><span>Design our Own</span><span>Pre-Register</span><span>Contact Us</span></nav>

  <svg class="abs" style="left:34px;top:330px" width="34" height="52" viewBox="0 0 34 52"><path d="M28 4 8 26l20 22" fill="none" stroke="#7ba0d0" stroke-width="4"/></svg>

  <div class="abs house" role="img" aria-label="3D cutaway render of a furnished modular home"></div>
  <div class="abs price"><b>$9,995</b><span>+ shipping</span></div>

  <h1 class="abs hero-title">1,000 homes<br>for $9,995 -<br><span class="hl">Register now</span></h1>
  <div class="abs contactless">Contactless Delivery is now available!</div>
  <div class="abs search"><svg width="10" height="16" viewBox="0 0 10 16" style="margin-top:2px"><path d="M5 0a5 5 0 0 0-5 5c0 4 5 11 5 11s5-7 5-11a5 5 0 0 0-5-5z" fill="#555"/><circle cx="5" cy="5" r="2" fill="#fff"/></svg>Enter your Location for delivery</div>
  <div class="abs search-btn">SEARCH</div>
  <div class="abs play"><svg width="62" height="62" viewBox="0 0 62 62"><path d="M24 18v26l21-13z" fill="#fff"/></svg></div>
  <div class="abs watch">WATCH VIDEO</div>
</section>

<section class="abs story">
  <svg class="abs" style="left:0;top:-20px" width="1200" height="110" viewBox="0 0 1200 110" preserveAspectRatio="none"><path d="M0 0h1200v40c-20 30-40 50-60 10-40 30-120 10-180 20-100 5-200 30-300 20-120-5-200 10-320 0-80 10-160 30-240 20-40-5-70-20-100 10z" fill="#0a55ad"/></svg>
</section>
<div class="abs sketch" role="img" aria-label="Line sketch of a glass-walled modular home interior"></div>
<div class="abs story-text">
  <div class="eyebrow">Our Team</div>
  <h2 class="section-title">The Story</h2>
  <p>Building a house should not be stressful – we believe it should be the happiest and one of the most rewarding experiences in your lifetime. So we set up our Happiness Brains Trust to troubleshoot how to remove the stress, delays and unexpected costs from building.</p>
  <p>The key problems our HBT came up with...and needed to solve:</p>
  <ul class="ticks">
    <li>Lack of tradesmen...and when you find them they can be VERY expensive.</li>
    <li>Lack of supply .... The waiting time on timber, widows, doors, etc is generally months or longer</li>
    <li>Lack of Communication – Getting all the tradies and suppliers to talk to each other and coordinate in a timely manner can be impossible and ends up costing months of delays.</li>
  </ul>
</div>
<div class="abs btn read-more">READ MORE</div>

<section class="abs register">
  <svg class="abs" style="left:0;top:-20px" width="1200" height="60" viewBox="0 0 1200 60" preserveAspectRatio="none"><path d="M0 20c40-10 80 20 130 5s90 15 150 2 100 18 170 4 110 12 180 0 120 15 190 3 100 12 170 0 80 10 210-4v40H0z" fill="#e8262f"/></svg>
</section>
<div class="abs reg-text">
  <div class="eyebrow">Register</div>
  <h2 class="section-title">Pre Register</h2>
  <ul class="ticks light">
    <li>To kickstart we are offering our first 1,000 houses for US$9,995</li>
    <li>All you need to do is give you name and email and you are registered.</li>
  </ul>
</div>
<div class="abs kitchen" role="img" aria-label="3D sketch of an open-plan kitchen and lounge"></div>

<div class="abs field" style="top:1566px">Full Name</div>
<div class="abs field" style="top:1631px">Email</div>
<div class="abs field" style="top:1695px">Phone Number</div>
<div class="abs field" style="top:1761px">No of home do you want to reserve</div>
<div class="abs choose">Choose one*</div>
<div class="abs radio" style="top:1904px">In under 20 words tell us why you deserve to be one of the first 1,000 people in the world to get a Brellix home.</div>
<div class="abs radio" style="top:1979px">Introduce 5 people to Brellix and get INSTANT approval.</div>
<div class="abs note" style="top:2035px">You will be asked to pay a $100 refundable deposit.</div>
<div class="abs note" style="top:2072px">When we give you a start date on the build, you will need to pay a 50% deposit. The balance is due once it is Quality tested and wrapped for shipping</div>
<div class="abs btn submit">SUBMIT</div>

<svg class="abs" style="left:0;top:2270px" width="1200" height="70" viewBox="0 0 1200 70" preserveAspectRatio="none"><path d="M0 30c150 0 400-8 600-5s300-20 420-15c60 2 100 30 140 40 15-25 30-25 40-22v42H0z" fill="#000"/></svg>

<div class="abs brand foot-logo" style="left:110px;top:2375px">
  <div class="brand-name">BRELLIX</div>
  <div class="brand-tag">DESIGN - BUILD - DELIVER</div>
</div>
<div class="abs foot-col" style="left:550px;top:2358px">
  <h4>QUICK LINKS</h4>
  <ul><li>Privacy</li><li>Terms &amp; Conditions</li><li>Investment</li><li>Media</li><li>NGO/Government</li><li>Contact</li><li>Sitemap</li></ul>
</div>
<div class="abs foot-col" style="left:807px;top:2358px;width:300px">
  <h4>CONTACT US</h4>
  <div class="contact-line"><svg width="9" height="13" viewBox="0 0 10 16"><path d="M5 0a5 5 0 0 0-5 5c0 4 5 11 5 11s5-7 5-11a5 5 0 0 0-5-5z" fill="#fff"/><circle cx="5" cy="5" r="2" fill="#000"/></svg>PO 417, Ashcombe, Victoria 3291, AUSTRALIA</div>
  <div class="contact-line" style="margin-top:22px"><svg width="12" height="12" viewBox="0 0 12 12"><path d="M2 0l3 3-1.5 1.5a8 8 0 0 0 4 4L9 7l3 3-2 2C5 12 0 7 0 2z" fill="#fff"/></svg>042 518 903</div>
  <h4 style="margin-top:30px">HOURS</h4>
  <div class="contact-line"><svg width="12" height="12" viewBox="0 0 12 12"><circle cx="6" cy="6" r="5" fill="none" stroke="#fff" stroke-width="2"/><path d="M6 3v3h2" stroke="#fff" stroke-width="1.5" fill="none"/></svg>Monday - Friday: 8am - 5pm<br>Saturday - Sunday: Closed</div>
</div>
<div class="abs rule"></div>
<div class="abs copy">Copyright © 2022 Brellix - All Rights Reserved.</div>
<div class="abs socials" aria-label="Social links"><span></span><span></span><span></span><span></span><span></span></div>

</body>
</html>
```